Print materials for 3-star hotel

We are changing up our print materials (notepads, letterheads, key card jackets, small flyer for the room rates) We are a 3 star business hotel in the Philippines and have mainly used grey tones and clean, simple lines. See attached photos for logo and hotel interior photos.

Target Market(s)

Business

Contact Information for Business Card

Corvale Terrace Hotel
Lindwell Banca Avenue corner Tolenta St Cebu City 6000 Philippines
Tel: +63 32 481 7302
Mobile: +63 917 648 2095
www.corvaleterracehotel.example

Font styles to use
Serif
Sans Serif

Requirements
Must have
• Simple
• Readable font and font size
Nice to have
• Neutral colors, grey and taupes
Should not have
• No purples and bright blues

```html
<!DOCTYPE html>
<html lang="en">
<head>
<meta charset="utf-8">
<title>Corvale Terrace Hotel – Business Card</title>
<link href="https://fonts.googleapis.com/css2?family=Roboto:wght@400;500&display=swap" rel="stylesheet">
<style>
  :root {
    --backdrop: #e3e3e1;
    --taupe: #b5a68a;
    --ink: #ffffff;
    --rule: rgba(255, 255, 255, 0.7);
  }
  * { margin: 0; padding: 0; box-sizing: border-box; }
  html, body {
    width: 1200px; height: 960px; overflow: hidden;
    background: var(--backdrop);
    font-family: "Roboto", Arial, sans-serif;
    color: var(--ink);
  }
  .stage { position: relative; width: 1200px; height: 960px; }
  .card {
    position: absolute; width: 600px; height: 342px;
    background: var(--taupe);
  }
  .card--front { left: 314px; top: 113px; }
  .card--back { left: 311px; top: 472px; }

  .brand {
    position: absolute; left: 40px; width: 272px; top: 120px;
    text-align: center;
  }
  .brand__mark {
    display: block; width: 14px; height: 14px; margin: 0 auto 12px;
    background: var(--ink);
  }
  .brand__name {
    font-weight: 400; font-size: 15px; letter-spacing: 3px;
    line-height: 20px; text-transform: uppercase;
  }

  .divider {
    position: absolute; left: 318px; top: 74px;
    width: 1px; height: 196px; background: var(--rule);
  }

  .details { position: absolute; left: 347px; top: 72px; }
  .details__name { font-size: 20px; font-weight: 500; line-height: 24px; letter-spacing: 0.2px; }
  .details__title { font-size: 14.5px; font-weight: 500; line-height: 18px; }
  .details__address { margin-top: 11px; font-size: 14px; line-height: 18px; }
  .contact-list { list-style: none; margin-top: 12px; }
  .contact-list li {
    display: flex; align-items: center; height: 19px;
    font-size: 14px;
  }
  .contact-list svg { width: 13px; height: 13px; margin-right: 10px; fill: var(--ink); flex: none; }

  .back-brand {
    position: absolute; left: 0; right: 0; top: 142px;
    text-align: center;
  }
  .back-brand .brand__name { font-size: 20px; letter-spacing: 5px; line-height: 26px; }
  .back-brand .brand__mark { width: 18px; height: 18px; margin-bottom: 14px; }
  .back-web {
    position: absolute; left: 0; right: 0; top: 286px;
    text-align: center; font-size: 14px; letter-spacing: 4.5px;
  }
</style>
</head>
<body>
<main class="stage">
  <section class="card card--front">
    <div class="brand">
      <span class="brand__mark"></span>
      <p class="brand__name">Corvale Terrace<br>Hotel</p>
    </div>
    <div class="divider"></div>
    <div class="details">
      <p class="details__name">ELENA MARSH</p>
      <p class="details__title">CEO/FOUNDER</p>
      <p class="details__address">412 Halvern Court<br>Brookfield, Oregon 58210</p>
      <ul class="contact-list">
        <li><svg viewBox="0 0 16 16"><path d="M3.6 1.2l2.3 2.6c.4.4.3 1-.1 1.4L4.6 6.3c.9 2 2.6 3.7 4.7 4.7l1.1-1.2c.4-.4 1-.5 1.4-.1l2.6 2.3c.4.4.4 1 0 1.4l-1.5 1.4C9.8 15.6.7 6.4 1.8 3.3l1.4-1.9c.1-.3.3-.3.4-.2z"/></svg>555 214 7780</li>
        <li><svg viewBox="0 0 16 16"><path d="M4.5 0h7c.8 0 1.5.7 1.5 1.5v13c0 .8-.7 1.5-1.5 1.5h-7C3.7 16 3 15.3 3 14.5v-13C3 .7 3.7 0 4.5 0zM4.6 2v10.5h6.8V2zM8 13.3a.9.9 0 100 1.8.9.9 0 000-1.8z"/></svg>555 306 1942</li>
        <li><svg viewBox="0 0 16 16"><path d="M4 1h8v4H4zM2 6h12c.6 0 1 .4 1 1v5h-3v3H4v-3H1V7c0-.6.4-1 1-1zm3 5v3h6v-3z"/></svg>555 719 4036</li>
        <li><svg viewBox="0 0 16 16"><path d="M1 3.5h14v1L8 9 1 4.5zM1 6l7 4.5L15 6v7H1z"/></svg>hello@corvaleterrace.example</li>
        <li><svg viewBox="0 0 16 16"><path d="M8 1a7 7 0 100 14A7 7 0 008 1zm-1 2.2c.6.9.3 1.8-.6 2.3-.8.4-1.1 1.2-.5 1.9.6.7 1.7.4 2.2 1.4.4.8-.2 1.9.3 2.8-.9.8-1.7 1.4-2.4 1.6-.2-1.2-.9-2.3-2-3-.9-.6-1.3-1.7-1.4-2.8C3.1 4.8 4.9 3.4 7 3.2zm4.4 1.5A5.3 5.3 0 0113 10c-.8-.3-1.4-1-1.5-1.9-.1-.9-.9-1.4-1.5-2 .4-.5.9-1 1.4-1.4z"/></svg>www.corvaleterracehotel.example</li>
      </ul>
    </div>
  </section>

  <section class="card card--back">
    <div class="back-brand">
      <span class="brand__mark"></span>
      <p class="brand__name">Corvale Terrace<br>Hotel</p>
    </div>
    <p class="back-web">www.corvaleterracehotel.example</p>
  </section>
</main>
</body>
</html>
```